Brellwick Partners, LLC Stationary

Brellwick Partners, LLC is a new financial planning and consulting company. We are looking for designs on business cards, letterhead, envelopes, and anything else that would be useful. Our preference for business card design is two sided. We are looking for a professional and clean look with incorporating the logo and patriotic feel. Thank you to all who participate and good luck!

```html
<!DOCTYPE html>
<html lang="en">
<head>
<meta charset="utf-8">
<title>Brellwick Partners, LLC – Business Card</title>
<link rel="stylesheet" href="https://fonts.googleapis.com/css2?family=Roboto:wght@400;500;700&display=swap">
<style>
  :root {
    --navy: #1d3f6e;
    --navy-deep: #16325a;
    --red: #c8202a;
    --red-deep: #8f1820;
    --white: #ffffff;
    --paper: #fbfbfb;
    --backdrop: #2b2d30;
    --ink-light: #e9eef5;
  }
  * { box-sizing: border-box; margin: 0; padding: 0; }
  html, body {
    width: 1200px; height: 950px; overflow: hidden;
    background: var(--backdrop);
    font-family: "Roboto", Arial, sans-serif;
  }
  .canvas { position: relative; width: 1200px; height: 950px; }
  .card {
    position: absolute; left: 250px; width: 700px; height: 400px;
    border-radius: 4px; overflow: hidden;
    box-shadow: 0 14px 30px rgba(0,0,0,.45);
  }
  .card--front { top: 50px; background: var(--paper); }
  .card--back {
    top: 500px;
    background: linear-gradient(100deg, var(--red) 0%, #b71c24 55%, var(--red-deep) 100%);
  }
  .front-art { position: absolute; inset: 0; }

  .brand { position: absolute; left: 48px; top: 52px; display: flex; align-items: center; gap: 14px; }
  .brand__dot { width: 22px; height: 22px; border-radius: 50%; background: var(--navy); }
  .brand__name { color: var(--navy); font-weight: 700; font-size: 30px; letter-spacing: .5px; }
  .brand__tagline {
    position: absolute; left: 84px; top: 96px;
    color: var(--navy); font-size: 11px; letter-spacing: 2.6px; text-transform: uppercase;
  }

  .person { position: absolute; left: 84px; top: 140px; }
  .person__name { color: var(--navy); font-weight: 700; font-size: 22px; }
  .person__title { color: var(--red); font-weight: 500; font-size: 17px; margin-top: 2px; }

  .contact { position: absolute; right: 40px; bottom: 20px; list-style: none; text-align: right; }
  .contact__item {
    display: flex; justify-content: flex-end; align-items: center; gap: 10px;
    color: var(--ink-light); font-size: 16px; line-height: 25px;
  }
  .contact__icon { width: 15px; height: 15px; fill: var(--ink-light); }
  .contact__item--plain { padding-right: 25px; }

  .back-brand {
    position: absolute; left: 0; right: 0; top: 150px;
    display: flex; justify-content: center; align-items: center; gap: 16px;
  }
  .back-brand__dot { width: 26px; height: 26px; border-radius: 50%; background: var(--white); opacity: .9; }
  .back-brand__name { color: var(--white); font-weight: 700; font-size: 36px; letter-spacing: .5px; }
  .back-web {
    position: absolute; left: 0; right: 0; top: 230px; text-align: center;
    color: rgba(255,255,255,.8); font-size: 16px; letter-spacing: 3px;
  }
</style>
</head>
<body>
<main class="canvas">

  <section class="card card--front" aria-label="Business card front">
    <svg class="front-art" viewBox="0 0 700 400" width="700" height="400" aria-hidden="true">
      <path d="M0,292 C260,400 500,250 700,110 L700,400 L0,400 Z" fill="var(--navy)"/>
      <path d="M0,278 C260,385 500,234 700,88 L700,102 C500,246 260,397 0,292 Z" fill="var(--red)"/>
    </svg>

    <div class="brand">
      <span class="brand__dot"></span>
      <span class="brand__name">Brellwick Partners, LLC</span>
    </div>
    <p class="brand__tagline">Financial Planning and Consulting</p>

    <div class="person">
      <p class="person__name">Marcus Hale</p>
      <p class="person__title">President</p>
    </div>

    <ul class="contact">
      <li class="contact__item">555 0142 2253
        <svg class="contact__icon" viewBox="0 0 16 16"><path d="M3 1l3 3-1.5 2a9 9 0 0 0 5.5 5.5L12 10l3 3-2 2C6 15 1 10 1 3z"/></svg>
      </li>
      <li class="contact__item">555 0187 3856
        <svg class="contact__icon" viewBox="0 0 16 16"><path d="M4 1h8v4H4zM1 6h14v7h-3v2H4v-2H1zM5 10v4h6v-4z"/></svg>
      </li>
      <li class="contact__item">marcus@brellwick.com
        <svg class="contact__icon" viewBox="0 0 16 16"><path d="M1 3h14v10H1zM2 4l6 5 6-5z" fill-rule="evenodd"/></svg>
      </li>
      <li class="contact__item">www.brellwick.com
        <svg class="contact__icon" viewBox="0 0 16 16"><circle cx="8" cy="8" r="7"/></svg>
      </li>
      <li class="contact__item contact__item--plain">2716 Linden Crest Drive</li>
      <li class="contact__item contact__item--plain">Harbor Vale, NY 10950</li>
    </ul>
  </section>

  <section class="card card--back" aria-label="Business card back">
    <div class="back-brand">
      <span class="back-brand__dot"></span>
      <span class="back-brand__name">Brellwick Partners, LLC</span>
    </div>
    <p class="back-web">www.brellwick.com</p>
  </section>

</main>
</body>
</html>
```